Holistic Health Coach needs simple web site design for a new practice

I need a web (re)design for my entire site, Ridgeway Fern Lady. I have a beautiful new blue and green logo that I'd like the site fonts and color scheme to be built around. I'll attach my new logo so you'll know the colors/design feel I'm after.

I want easy navigation for my mostly text based site, widgets for my social media pages and a clean, fun, light feel for the site.

Target Market(s)

People looking to take charge of their own health, and who may need my coaching services to obtain optimal wellness.

Industry/Entity Type

Health

Coding

Coded - Design and coding required

Number of Pages Required

5+ page

Font styles to use
Script

Colors
33b8a4
33a6d7
ffffff

Requirements
Must have
• Must incorporate my logo design, as well as same/similar fonts and color scheme.
• I'd like it to stay as close to the current design as possible.
Nice to have
• Would love to incorporate a hover over menu (for example, when a user hovers over "About", they will see the submenu in a floating design.
Should not have
• No dark colors or masculine feel

```html
<!DOCTYPE html>
<html lang="en">
<head>
<meta charset="utf-8">
<title>Ridgeway Fern Lady — Holistic Health Coaching</title>
<link href="https://fonts.googleapis.com/css2?family=Mulish:wght@400;600;700&display=swap" rel="stylesheet">
<style>
:root{
  --green:#33b8a4;
  --green-dark:#27a28f;
  --blue:#33a6d7;
  --blue-dark:#2390c2;
  --white:#ffffff;
  --page:#f6f6f6;
  --line:#e2e2e2;
  --ink:#3a3a3a;
  --muted:#8a8a8a;
  --dark-head:#4b4b4b;
  --footer:#262626;
  --footer-bar:#1b1b1b;
  --orange:#f39a1e;
}
*{box-sizing:border-box;margin:0;padding:0}
html,body{width:1200px;height:3309px;overflow:hidden}
body{position:relative;background:var(--page);font-family:"Mulish",Arial,sans-serif;color:var(--ink)}
a{color:inherit;text-decoration:none}
ul{list-style:none}

/* header */
.site-header{position:absolute;left:0;top:0;width:1200px;height:121px;background:var(--white)}
.brand{position:absolute;left:0;width:1200px;top:46px;text-align:center;font-size:36px;font-weight:700;color:var(--green);letter-spacing:.5px}
.brand-dot{display:inline-block;width:14px;height:14px;border-radius:50%;background:var(--blue);margin-right:12px;vertical-align:middle}

.main-nav{position:absolute;left:0;top:121px;width:1200px;height:55px;background:linear-gradient(var(--blue),var(--blue-dark))}
.main-nav li{position:absolute;top:0;height:55px;line-height:55px;font-size:13px;color:var(--white);letter-spacing:.3px;text-align:center}
.main-nav .is-active{background:var(--green)}
.submenu{position:absolute;left:205px;top:181px;width:192px;height:172px;background:var(--green);padding:8px 0 0 18px;z-index:3}
.submenu li{font-size:13px;color:var(--white);line-height:32px}

/* hero */
.hero{position:absolute;left:99px;top:181px;width:1002px;height:441px;background:linear-gradient(110deg,#6f8f4a 0%,#a7b96a 35%,#d8c9a0 55%,#4c5a3a 80%,#2e3524 100%)}
.hero-arrows{position:absolute;left:14px;bottom:14px;display:flex;gap:3px}
.hero-arrows span{width:26px;height:26px;background:rgba(40,40,40,.75);display:flex;align-items:center;justify-content:center}

/* main column */
.main-col{position:absolute;left:99px;top:662px;width:680px}
.section-head{height:44px;line-height:44px;padding-left:16px;font-size:22px;color:var(--white);background:var(--blue);position:relative}
.section-head.is-dark{background:var(--dark-head)}
.main-col > .section-head{margin-bottom:29px}

.post-card{height:580px;background:var(--white);border:1px solid var(--line);padding:30px 15px 0;margin-bottom:12px;position:relative}
.post-head{display:flex;gap:16px;height:75px;padding-left:2px}
.post-badge{width:44px;height:44px;border:2px solid var(--green);border-radius:50%;display:flex;align-items:center;justify-content:center;flex:none;margin-top:6px}
.post-title{font-size:16px;font-weight:400;color:var(--ink);margin-top:6px;white-space:nowrap}
.post-meta{display:flex;gap:26px;font-size:11px;color:var(--ink);margin-top:14px}
.post-meta span{display:flex;align-items:center;gap:5px}
.post-meta b{font-weight:400;color:var(--green);text-decoration:underline}
.post-photo{height:314px}
.post-excerpt{font-size:12px;line-height:23px;color:#6a6a6a;margin-top:22px;height:72px}
.share-row{position:absolute;left:0;right:0;bottom:0;height:56px;border-top:1px solid var(--line);display:flex;align-items:center}
.share-row i{flex:1;display:flex;justify-content:center}
.share-row i::before{content:"";width:9px;height:9px;border-radius:50%;background:#555}
.share-row .mail::before{display:none}
.share-row .read-more{flex:1.3;font-size:13px;color:var(--green);text-align:center}

.photo-lounge{background:linear-gradient(100deg,#d9c7a5 0%,#b4bfc2 40%,#6aa7c7 70%,#2f7fae 100%)}
.photo-kitchen{background:linear-gradient(100deg,#e8ece6 0%,#c9cec4 45%,#d65a3e 65%,#7b6a58 100%)}
.photo-yoga{background:linear-gradient(180deg,#8fc0e2 0%,#c8e1f0 45%,#2c6fa0 60%,#1d4f78 100%)}

.recent-posts{margin-top:-1px}
.recent-posts .section-head{margin-bottom:28px}
.recent-grid{display:flex;gap:21px}
.recent-item{width:329px}
.recent-photo{height:199px}
.recent-photo.family{background:linear-gradient(120deg,#7a4c3a,#c4946e 50%,#e6d1b4)}
.recent-photo.reader{background:linear-gradient(120deg,#3b2a22,#a5653c 45%,#d9b583 75%,#6d7a56)}
.recent-item h3{font-size:14px;font-weight:600;margin-top:22px}
.recent-meta{font-size:11px;color:var(--muted);margin-top:12px;display:flex;gap:14px}
.recent-item p{font-size:12px;line-height:22px;color:#6a6a6a;margin-top:14px}

.pagination{margin-top:44px;display:flex;gap:20px;font-size:14px;font-weight:700;color:var(--ink);align-items:center}
.pagination .is-current{color:#d64040;position:relative}
.pagination .is-current::after{content:"";position:absolute;left:3px;top:22px;width:0;height:0;border:4px solid transparent;border-top-color:#222}

/* sidebar */
.sidebar{position:absolute;left:818px;top:662px;width:283px}
.widget{background:var(--white);border:1px solid var(--line);margin-bottom:25px}
.widget-title{font-size:20px;color:var(--ink);padding:14px 9px 0}
.social-box{height:101px}
.social-buttons{display:flex;gap:5px;padding:14px 8px 0}
.social-buttons span{height:22px;padding:0 8px;line-height:22px;font-size:9px;color:var(--white)}
.newsletter{height:249px}
.newsletter form{padding:16px 11px 0}
.newsletter input{display:block;width:260px;height:32px;border:1px solid var(--line);background:#fafafa;margin-bottom:12px;padding-left:10px;font:11px "Mulish",Arial,sans-serif;color:#555}
.newsletter button{display:block;margin:6px auto 0;width:223px;height:44px;border:none;background:linear-gradient(var(--green),var(--green-dark));font:700 13px "Mulish",Arial,sans-serif;color:#165f54;letter-spacing:.4px}

.comments-widget{margin-bottom:30px}
.comments-widget .section-head,.list-widget .section-head{height:42px;line-height:42px;font-size:20px;padding-left:14px}
.comment-list{border:1px solid var(--line);border-top:none;background:var(--white);padding:14px 0 6px}
.comment-item{display:flex;gap:20px;height:112px;padding:8px 0 0 3px;border-bottom:1px solid var(--line)}
.comment-item:last-child{border-bottom:none}
.comment-thumb{width:90px;height:80px;flex:none}
.comment-item p{font-size:11px;line-height:19px;color:#6a6a6a;margin-top:4px}
.comment-item small{display:block;font-size:10px;color:var(--muted);margin-top:12px}

.promo{height:274px;background:linear-gradient(#e9e9ea,#dcdcde);margin-bottom:31px;position:relative;text-align:center;padding-top:8px}
.promo h4{font-size:17px;font-weight:700;color:#2c2c2c;line-height:22px;letter-spacing:.3px}
.promo h4 em{font-style:normal;color:var(--blue)}
.promo-art{position:absolute;left:12px;top:100px;width:150px;height:84px;background:linear-gradient(90deg,#6bb5c0,#8c6bb3,#e1a14c)}
.promo-seal{position:absolute;left:180px;top:96px;width:84px;height:84px;border-radius:50%;background:var(--blue)}
.promo p{position:absolute;left:0;right:0;top:190px;font-size:26px;color:#4a4a4a}
.promo-button{position:absolute;left:60px;top:230px;width:158px;height:38px;line-height:38px;background:var(--orange);color:var(--white);font-size:16px;font-weight:700;border-radius:3px}

.list-widget{margin-bottom:31px}
.list-widget ul{border:1px solid var(--line);border-top:none;background:var(--white);padding:20px 0 12px 12px}
.list-widget li{display:flex;align-items:center;gap:14px;height:32.5px;font-size:12px;color:#6a6a6a}

/* footer */
.site-footer{position:absolute;left:0;top:3022px;width:1200px;height:232px;background:var(--footer);color:#cfcfcf}
.footer-col{position:absolute;top:46px}
.footer-col h5{font-size:18px;font-weight:400;color:var(--white);margin-bottom:18px}
.footer-col p{font-size:10px;line-height:17px;color:#bdbdbd}
.footer-social{display:flex;gap:16px;margin-top:26px}
.footer-social span{width:18px;height:18px;border-radius:50%;background:#e8e8e8}
.tweet{display:flex;gap:10px}
.tweet strong{display:block;font-size:10px;color:var(--white);font-weight:600;margin-bottom:8px}
.tweet a{display:block;font-size:10px;color:var(--green);text-decoration:underline;margin-top:18px}
.snap-grid{display:grid;grid-template-columns:repeat(3,56px);gap:3px}
.snap-grid span{height:28px}
.contact dl{display:grid;grid-template-columns:58px 150px;row-gap:14px;font-size:10px;line-height:14px}
.contact dt{color:var(--white);font-weight:600}
.contact dd{color:#bdbdbd}

.footer-bar{position:absolute;left:0;top:3254px;width:1200px;height:55px;background:var(--footer-bar);font-size:10px;color:#bdbdbd}
.footer-bar nav{position:absolute;left:99px;top:20px;display:flex;gap:10px}
.footer-bar .copyright{position:absolute;right:99px;top:20px}
</style>
</head>
<body>

<header class="site-header">
  <div class="brand"><span class="brand-dot"></span>Ridgeway Fern Lady</div>
</header>

<nav class="main-nav">
  <ul>
    <li style="left:136px;width:38px">HOME</li>
    <li class="is-active" style="left:205px;width:130px">ABOUT MAREN</li>
    <li style="left:360px;width:76px">ARTICLES</li>
    <li style="left:476px;width:118px">ESSENTIAL OILS</li>
    <li style="left:630px;width:306px">21-DAY SWEET RESET COACHING SERVICES</li>
    <li style="left:975px;width:94px">CONTACT US</li>
  </ul>
</nav>
<ul class="submenu">
  <li>Lorem Ipsum is Dummy</li>
  <li>Lorem Ipsum is Dummy</li>
  <li>Lorem Ipsum is Dummy</li>
  <li>Lorem Ipsum is Dummy</li>
  <li>Lorem Ipsum is Dummy</li>
</ul>

<section class="hero" role="img" aria-label="Woman reading a book while sitting under a tree in a sunny park">
  <div class="hero-arrows">
    <span><svg width="10" height="10" viewBox="0 0 10 10"><path d="M7 1 3 5l4 4" stroke="#fff" stroke-width="1.6" fill="none"/></svg></span>
    <span><svg width="10" height="10" viewBox="0 0 10 10"><path d="M3 1l4 4-4 4" stroke="#fff" stroke-width="1.6" fill="none"/></svg></span>
  </div>
</section>

<main class="main-col">
  <h2 class="section-head">Latest Blog</h2>

  <article class="post-card">
    <div class="post-head">
      <span class="post-badge"><svg width="18" height="18" viewBox="0 0 18 18"><path d="M3 15l1-4 8-8 3 3-8 8z" fill="var(--green)"/></svg></span>
      <div>
        <h3 class="post-title">Lifestyles of the Tired and Wired – Module 4 of Whole Reset Rehab : Adrenal Fatigue</h3>
        <div class="post-meta">
          <span><svg width="11" height="10" viewBox="0 0 11 10"><path d="M1 4h2l6-3v8L3 6H1z" fill="#555"/></svg>Published in <b>Photography</b></span>
          <span><svg width="11" height="11" viewBox="0 0 11 11"><path d="M1 10l1-3 6-6 2 2-6 6z" fill="none" stroke="#555"/></svg>Written by <b>Admin</b></span>
          <span><svg width="12" height="10" viewBox="0 0 12 10"><path d="M1 1h10v6H5L2 9V7H1z" fill="none" stroke="#555"/></svg>Comments <b>277</b></span>
        </div>
      </div>
    </div>
    <div class="post-photo photo-lounge" role="img" aria-label="Smiling woman relaxing in a rattan lounge chair with blue cushions"></div>
    <p class="post-excerpt">He first lesson in Module 4 covered stress management. There was a video discussing the effects of stress on the body, why stress management is so important, and several ideas that you can implement right away to help minimize I selected. I am starting to see a difference in my mood and energy levels……</p>
    <div class="share-row"><i></i><i></i><i></i><i></i><i></i><i></i><i class="mail"><svg width="13" height="10" viewBox="0 0 13 10"><rect x=".5" y=".5" width="12" height="9" fill="none" stroke="#555"/><path d="M.5.5l6 5 6-5" fill="none" stroke="#555"/></svg></i><a class="read-more">Read More</a></div>
  </article>

  <article class="post-card">
    <div class="post-head">
      <span class="post-badge"><svg width="18" height="18" viewBox="0 0 18 18"><path d="M3 15l1-4 8-8 3 3-8 8z" fill="var(--green)"/></svg></span>
      <div>
        <h3 class="post-title">April Essential Living Education Series</h3>
        <div class="post-meta">
          <span><svg width="11" height="10" viewBox="0 0 11 10"><path d="M1 4h2l6-3v8L3 6H1z" fill="#555"/></svg>Published in <b>Photography</b></span>
          <span><svg width="11" height="11" viewBox="0 0 11 11"><path d="M1 10l1-3 6-6 2 2-6 6z" fill="none" stroke="#555"/></svg>Written by <b>Admin</b></span>
          <span><svg width="12" height="10" viewBox="0 0 12 10"><path d="M1 1h10v6H5L2 9V7H1z" fill="none" stroke="#555"/></svg>Comments <b>277</b></span>
        </div>
      </div>
    </div>
    <div class="post-photo photo-kitchen" role="img" aria-label="Woman in a red cardigan cooking vegetables in a bright kitchen"></div>
    <p class="post-excerpt">He first lesson in Module 4 covered stress management. There was a video discussing the effects of stress on the body, why stress management is so important, and several ideas that you can implement right away to help minimize I selected. I am starting to see a difference in my mood and energy levels……</p>
    <div class="share-row"><i></i><i></i><i></i><i></i><i></i><i></i><i class="mail"><svg width="13" height="10" viewBox="0 0 13 10"><rect x=".5" y=".5" width="12" height="9" fill="none" stroke="#555"/><path d="M.5.5l6 5 6-5" fill="none" stroke="#555"/></svg></i><a class="read-more">Read More</a></div>
  </article>

  <article class="post-card">
    <div class="post-head">
      <span class="post-badge"><svg width="18" height="18" viewBox="0 0 18 18"><path d="M3 15l1-4 8-8 3 3-8 8z" fill="var(--green)"/></svg></span>
      <div>
        <h3 class="post-title">April Essential Living Education Series</h3>
        <div class="post-meta">
          <span><svg width="11" height="10" viewBox="0 0 11 10"><path d="M1 4h2l6-3v8L3 6H1z" fill="#555"/></svg>Published in <b>Photography</b></span>
          <span><svg width="11" height="11" viewBox="0 0 11 11"><path d="M1 10l1-3 6-6 2 2-6 6z" fill="none" stroke="#555"/></svg>Written by <b>Admin</b></span>
          <span><svg width="12" height="10" viewBox="0 0 12 10"><path d="M1 1h10v6H5L2 9V7H1z" fill="none" stroke="#555"/></svg>Comments <b>277</b></span>
        </div>
      </div>
    </div>
    <div class="post-photo photo-yoga" role="img" aria-label="Woman in white meditating in a yoga pose by the sea"></div>
    <p class="post-excerpt">He first lesson in Module 4 covered stress management. There was a video discussing the effects of stress on the body, why stress management is so important, and several ideas that you can implement right away to help minimize I selected. I am starting to see a difference in my mood and energy levels……</p>
    <div class="share-row"><i></i><i></i><i></i><i></i><i></i><i></i><i class="mail"><svg width="13" height="10" viewBox="0 0 13 10"><rect x=".5" y=".5" width="12" height="9" fill="none" stroke="#555"/><path d="M.5.5l6 5 6-5" fill="none" stroke="#555"/></svg></i><a class="read-more">Read More</a></div>
  </article>

  <section class="recent-posts">
    <h2 class="section-head is-dark">Recent Posts</h2>
    <div class="recent-grid">
      <article class="recent-item">
        <div class="recent-photo family" role="img" aria-label="Family reading a book together on a sofa"></div>
        <h3>A Nice Supplement to the Program</h3>
        <div class="recent-meta"><span>Posted by Join</span><span>/</span><span>2 Comments</span><span>/</span><span>6 Hours ago</span></div>
        <p>He first lesson in Module 4 covered stress management. There was a video discussing the effects of stress on the mood and energy levels……</p>
      </article>
      <article class="recent-item">
        <div class="recent-photo reader" role="img" aria-label="Woman reading outdoors in warm evening light"></div>
        <h3>A Nice Supplement to the Program</h3>
        <div class="recent-meta"><span>Posted by Join</span><span>/</span><span>2 Comments</span><span>/</span><span>6 Hours ago</span></div>
        <p>He first lesson in Module 4 covered stress management. There was a video discussing the effects of stress on the mood and energy levels……</p>
      </article>
    </div>
    <nav class="pagination"><span>«</span><span>1</span><span>2</span><span class="is-current">3</span><span>4</span><span>»</span></nav>
  </section>
</main>

<aside class="sidebar">
  <section class="widget social-box">
    <h3 class="widget-title">Social share-bar</h3>
    <div class="social-buttons">
      <span style="background:#3aa9e0">Chirp</span>
      <span style="background:#d9493a">Circles</span>
      <span style="background:#3b5998">Friends</span>
      <span style="background:#cb2027">Boards</span>
    </div>
  </section>

  <section class="widget newsletter">
    <h3 class="widget-title">Newsletter Sign up</h3>
    <form>
      <input type="text" placeholder="Enter Your Name :">
      <input type="text" placeholder="Enter Your Phone :">
      <input type="text" placeholder="Enter Your Email :">
      <button type="button">SUBSCRIBE NOW!</button>
    </form>
  </section>

  <section class="comments-widget">
    <h3 class="section-head is-dark">Recent Comments</h3>
    <ul class="comment-list">
      <li class="comment-item">
        <div class="comment-thumb" role="img" aria-label="Bowl of fresh salad" style="background:linear-gradient(135deg,#e9e4d8,#c74b3b 55%,#6f9a43)"></div>
        <div><p>The final lesson covers exercise one will  Health community.</p><small>2 Comments &nbsp;/&nbsp; 6 Hours ago</small></div>
      </li>
      <li class="comment-item">
        <div class="comment-thumb" role="img" aria-label="Friends smiling together" style="background:linear-gradient(135deg,#d9c2a4,#b57a52 50%,#6e4a35)"></div>
        <div><p>The final lesson covers exercise one will  Health community.</p><small>2 Comments &nbsp;/&nbsp; 6 Hours ago</small></div>
      </li>
      <li class="comment-item">
        <div class="comment-thumb" role="img" aria-label="Person reading outdoors at sunset" style="background:linear-gradient(135deg,#3b2a22,#b36f3f 50%,#e2c08a)"></div>
        <div><p>The final lesson covers exercise one will  Health community.</p><small>2 Comments &nbsp;/&nbsp; 6 Hours ago</small></div>
      </li>
    </ul>
  </section>

  <section class="promo">
    <h4>NEED <em>EXTRA SUPPORT</em><br>TO <em>ROCK</em> YOUR<br>21-DAY SWEET RESET?</h4>
    <div class="promo-art" role="img" aria-label="Row of program guidebooks"></div>
    <div class="promo-seal"></div>
    <p>I’m here to help</p>
    <a class="promo-button">TELL ME MORE!</a>
  </section>

  <section class="list-widget">
    <h3 class="section-head">Archives</h3>
    <ul>
      <li><svg width="16" height="16" viewBox="0 0 16 16"><circle cx="8" cy="8" r="7" fill="none" stroke="#999"/><path d="M7 5l3 3-3 3" fill="none" stroke="#999"/></svg>April 2015</li>
      <li><svg width="16" height="16" viewBox="0 0 16 16"><circle cx="8" cy="8" r="7" fill="none" stroke="#999"/><path d="M7 5l3 3-3 3" fill="none" stroke="#999"/></svg>March 2015</li>
      <li><svg width="16" height="16" viewBox="0 0 16 16"><circle cx="8" cy="8" r="7" fill="none" stroke="#999"/><path d="M7 5l3 3-3 3" fill="none" stroke="#999"/></svg>February 2015</li>
      <li><svg width="16" height="16" viewBox="0 0 16 16"><circle cx="8" cy="8" r="7" fill="none" stroke="#999"/><path d="M7 5l3 3-3 3" fill="none" stroke="#999"/></svg>January 2015</li>
      <li><svg width="16" height="16" viewBox="0 0 16 16"><circle cx="8" cy="8" r="7" fill="none" stroke="#999"/><path d="M7 5l3 3-3 3" fill="none" stroke="#999"/></svg>September 2014</li>
      <li><svg width="16" height="16" viewBox="0 0 16 16"><circle cx="8" cy="8" r="7" fill="none" stroke="#999"/><path d="M7 5l3 3-3 3" fill="none" stroke="#999"/></svg>June 2014</li>
      <li><svg width="16" height="16" viewBox="0 0 16 16"><circle cx="8" cy="8" r="7" fill="none" stroke="#999"/><path d="M7 5l3 3-3 3" fill="none" stroke="#999"/></svg>May 2014</li>
      <li><svg width="16" height="16" viewBox="0 0 16 16"><circle cx="8" cy="8" r="7" fill="none" stroke="#999"/><path d="M7 5l3 3-3 3" fill="none" stroke="#999"/></svg>April 2014</li>
    </ul>
  </section>

  <section class="list-widget">
    <h3 class="section-head is-dark">Categories</h3>
    <ul>
      <li><svg width="16" height="16" viewBox="0 0 16 16"><circle cx="8" cy="8" r="7" fill="none" stroke="#999"/><path d="M7 5l3 3-3 3" fill="none" stroke="#999"/></svg>21 Day Sweet Reset</li>
      <li><svg width="16" height="16" viewBox="0 0 16 16"><circle cx="8" cy="8" r="7" fill="none" stroke="#999"/><path d="M7 5l3 3-3 3" fill="none" stroke="#999"/></svg>Adrenal Fatigue</li>
      <li><svg width="16" height="16" viewBox="0 0 16 16"><circle cx="8" cy="8" r="7" fill="none" stroke="#999"/><path d="M7 5l3 3-3 3" fill="none" stroke="#999"/></svg>Articles</li>
      <li><svg width="16" height="16" viewBox="0 0 16 16"><circle cx="8" cy="8" r="7" fill="none" stroke="#999"/><path d="M7 5l3 3-3 3" fill="none" stroke="#999"/></svg>DIY</li>
    </ul>
  </section>
</aside>

<footer class="site-footer">
  <div class="footer-col" style="left:108px;width:170px">
    <h5>Stay in Touch!</h5>
    <p>Follow US in our social network! Lorem ipsum dolor sit amet, conse ctetur and go adipiscing elit.</p>
    <div class="footer-social"><span></span><span></span><span></span><span></span></div>
  </div>
  <div class="footer-col" style="left:362px;width:220px">
    <h5>Latest Updates</h5>
    <div class="tweet">
      <svg width="14" height="12" viewBox="0 0 14 12"><path d="M1 1h12v7H6L3 11V8H1z" fill="#bdbdbd"/></svg>
      <div>
        <strong>Sed ut perspiciatis unde omnis</strong>
        <p>A gentle reminder that small daily habits add up. New class schedule and recipes now posted on our site.</p>
        <a>http://www.ridgewayfernlady.com</a>
      </div>
    </div>
  </div>
  <div class="footer-col" style="left:627px;width:180px">
    <h5>Snapshots</h5>
    <div class="snap-grid" role="img" aria-label="Grid of recent photos from the practice">
      <span style="background:#c9a47a"></span><span style="background:#7e8fa8"></span><span style="background:#d7c08c"></span>
      <span style="background:#e0c23a"></span><span style="background:#6c5a8a"></span><span style="background:#3f6fa6"></span>
      <span style="background:#9a6a4a"></span><span style="background:#b0b5c7"></span><span style="background:#4a5a8a"></span>
    </div>
  </div>
  <div class="footer-col contact" style="left:882px;width:220px">
    <h5>Contact Us</h5>
    <dl>
      <dt>Address:</dt><dd>214 Fernbrook Lane, Suite 8, Ridgeway</dd>
      <dt>Phone:</dt><dd>+(000)-555-0142</dd>
      <dt>Email:</dt><dd style="color:var(--green)">hello@ridgewayfernlady.com</dd>
    </dl>
  </div>
</footer>

<div class="footer-bar">
  <nav><span>HOME</span><span>/</span><span>ABOUT MAREN</span><span>/</span><span>ARTICLES</span><span>/</span><span>ESSENTIAL</span><span>/</span><span>OILS 21-DAY SWEET RESET COACHING SERVICES</span></nav>
  <span class="copyright">© Copyright 2015 Ridgeway Fern Lady All Rights Reserved</span>
</div>

</body>
</html>
```